Business Cards for a law firm

Business cards for our law firm. Use our silhoette logo and OAK PARTNERS - check our website (www.oakpartners.example)

Contact Information for Business Card

our silhouette logo, OAK PARTNERS, 800-555-0147, Dorian Pemberton, dorian@oakpartners.example

Requirements
Must have
• our silhouette logo, OAK PARTNERS, 800-555-0147, Dorian Pemberton, dorian@oakpartners.example

```html
<!DOCTYPE html>
<html lang="en">
<head>
<meta charset="utf-8">
<title>Oak Partners – Business Cards</title>
<link rel="stylesheet" href="https://fonts.googleapis.com/css2?family=Montserrat:wght@400;700&family=Tenor+Sans&display=swap">
<style>
  :root {
    --page-bg: #e2e7e9;
    --navy: #22346b;
    --navy-deep: #1d2d5f;
    --sky: #3a94d4;
    --card-white: #ffffff;
    --ink: #26376d;
  }
  html, body {
    margin: 0;
    width: 1200px;
    height: 960px;
    overflow: hidden;
    background: var(--page-bg);
  }
  .sheet {
    position: relative;
    width: 1200px;
    height: 960px;
  }
  .card {
    position: absolute;
    left: 250px;
    width: 701px;
    height: 400px;
    overflow: hidden;
  }
  .card--front { top: 60px; background: var(--navy); }
  .card--back  { top: 500px; background: var(--card-white); }

  .front-pattern {
    position: absolute;
    inset: 0;
    width: 100%;
    height: 100%;
  }
  .brand-mark {
    position: absolute;
    left: 124px;
    top: 152px;
    width: 100px;
    height: 100px;
    background: var(--card-white);
  }
  .wordmark {
    position: absolute;
    left: 239px;
    top: 143px;
    margin: 0;
    font-family: "Tenor Sans", sans-serif;
    font-weight: 400;
    font-size: 53px;
    line-height: 47px;
    letter-spacing: 2px;
    color: var(--card-white);
  }
  .wordmark span { display: block; }

  .contact {
    position: absolute;
    left: 0;
    right: 0;
    top: 184px;
    text-align: center;
    color: var(--ink);
    font-family: "Montserrat", sans-serif;
  }
  .contact__name {
    margin: 0 0 38px;
    font-size: 33px;
    line-height: 34px;
    letter-spacing: 1.5px;
    text-transform: uppercase;
    font-weight: 400;
  }
  .contact__name strong { font-weight: 700; }
  .contact__line {
    margin: 0;
    font-family: "Tenor Sans", sans-serif;
    text-transform: uppercase;
    font-size: 16px;
    line-height: 24px;
    letter-spacing: 1px;
  }
  .contact__line--phone { font-size: 21px; }
</style>
</head>
<body>
<main class="sheet">
  <section class="card card--front">
    <svg class="front-pattern" viewBox="0 0 701 400" role="img" aria-label="Repeating pattern of small brand silhouettes fading from navy to bright blue towards the top right" preserveAspectRatio="none">
      <defs>
        <radialGradient id="pattern-glow" cx="1" cy="0" r="1.1">
          <stop offset="0" stop-color="#3a94d4" stop-opacity="0.9"/>
          <stop offset="0.55" stop-color="#2c5ea8" stop-opacity="0.55"/>
          <stop offset="1" stop-color="#1d2d5f" stop-opacity="0"/>
        </radialGradient>
      </defs>
      <rect width="701" height="400" fill="#22346b"/>
      <rect width="701" height="400" fill="url(#pattern-glow)"/>
    </svg>
    <div class="brand-mark" aria-hidden="true"></div>
    <h1 class="wordmark"><span>OAK</span><span>PARTNERS</span></h1>
  </section>

  <section class="card card--back">
    <div class="contact">
      <h2 class="contact__name"><strong>Dorian</strong> Pemberton</h2>
      <p class="contact__line contact__line--phone">800-555-0147</p>
      <p class="contact__line">www.oakpartners.example</p>
      <p class="contact__line">dorian@oakpartners.example</p>
    </div>
  </section>
</main>
</body>
</html>
```